Gift Card and Gift Card Holder Design

Hello I need a design for a gift card and the gift card holder. I am uploading two PDFs for examples of designs we used for other promotional flyers. I am also uploading some design templates - two gift card holder templates (each would require the same design) and one gift card template. Also attached are two images of another gift card design - simple front, back had areas for text. We will need these areas for text in the design. We will provide copy for those areas but we should be able to edit following the close of the design project with you.

Font styles to use
Sans Serif

Colors
ec1f27
0455a3

Requirements
Must have
• use this web site for color reference: https://quorvelfit.com/
• use this website for design inspiration for custom gift card holders: https://plintaroworks.com/customgiftcardholder.html
• option with $75 on front of card as value
• two more options without

```html
<!DOCTYPE html>
<html lang="en">
<head>
<meta charset="utf-8">
<title>Brenlow Window Blinds – Gift Card</title>
<link href="https://fonts.googleapis.com/css2?family=Archivo+Black&family=Oswald:wght@600&display=swap" rel="stylesheet">
<style>
  :root {
    --brand-red: #a30a0a;
    --brand-red-deep: #5e0606;
    --brand-blue: #0a1fd0;
    --brand-blue-deep: #061a7a;
    --die-cut: #1d1f1f;
    --wood-light: #d9dcdc;
    --wood-mid: #b4b8b8;
    --wood-warm: #c9bfb8;
    --ink-white: #ffffff;
  }
  html, body {
    margin: 0;
    padding: 0;
    width: 1200px;
    height: 754px;
    overflow: hidden;
    background: #ffffff;
  }
  .gift-card {
    display: block;
    width: 1200px;
    height: 754px;
  }
  .brand-name {
    font-family: "Archivo Black", "Arial Black", sans-serif;
    fill: var(--brand-blue);
  }
  .brand-slogan {
    font-family: "Archivo Black", "Arial Black", sans-serif;
    fill: var(--ink-white);
  }
  .company-heading {
    font-family: "Archivo Black", "Arial Black", sans-serif;
  }
  .company-heading .heading-name { fill: var(--brand-red); }
  .company-heading .heading-trade { fill: var(--brand-blue); }
  .tagline {
    font-family: "Archivo Black", "Arial Black", sans-serif;
    fill: var(--ink-white);
  }
  .card-title {
    font-family: "Oswald", "Arial Narrow", sans-serif;
    font-weight: 600;
  }
  .die-cut { fill: var(--die-cut); }
</style>
</head>
<body>
<svg class="gift-card" viewBox="0 0 1200 754" xmlns="http://www.w3.org/2000/svg">
  <defs>
    <linearGradient id="wood-tone" x1="0" y1="0" x2="1" y2="1">
      <stop offset="0" stop-color="var(--wood-mid)"/>
      <stop offset="0.45" stop-color="var(--wood-light)"/>
      <stop offset="1" stop-color="var(--wood-warm)"/>
    </linearGradient>
    <linearGradient id="title-red" x1="0" y1="0" x2="0" y2="1">
      <stop offset="0" stop-color="var(--brand-red-deep)"/>
      <stop offset="1" stop-color="var(--brand-red)"/>
    </linearGradient>
    <linearGradient id="title-blue" x1="0" y1="0" x2="0" y2="1">
      <stop offset="0" stop-color="var(--brand-blue-deep)"/>
      <stop offset="1" stop-color="var(--brand-blue)"/>
    </linearGradient>
    <filter id="soft-shadow" x="-10%" y="-10%" width="120%" height="140%">
      <feDropShadow dx="2" dy="3" stdDeviation="2" flood-color="#000" flood-opacity="0.45"/>
    </filter>
  </defs>

  <rect class="backdrop" x="0" y="0" width="1200" height="754" fill="url(#wood-tone)"
        role="img" aria-label="Weathered whitewashed wood planks with a faint room interior showing through"/>

  <g class="brand-block">
    <rect x="44" y="43" width="130" height="130" fill="var(--brand-red)"/>
    <text class="brand-name" x="44" y="284" font-size="90" textLength="318" lengthAdjust="spacingAndGlyphs">Brenlow</text>
    <text class="brand-slogan" x="45" y="326" font-size="29" textLength="317" lengthAdjust="spacingAndGlyphs" filter="url(#soft-shadow)">Installed Solutions</text>
  </g>

  <rect class="die-cut" x="502" y="67" width="199" height="44" rx="22"/>
  <rect class="die-cut" x="1090" y="278" width="43" height="198" rx="21.5"/>
  <circle class="die-cut" cx="89" cy="670" r="44"/>

  <text class="company-heading" x="387" y="183" font-size="66" textLength="770" lengthAdjust="spacingAndGlyphs"><tspan class="heading-name">Brenlow</tspan> <tspan class="heading-trade">Window Blinds</tspan></text>
  <text class="tagline" x="388" y="205" font-size="14" textLength="769" lengthAdjust="spacingAndGlyphs" filter="url(#soft-shadow)">The preferred installer of window treatments to the builder, homeowner, and remodelers.</text>

  <g class="card-title" filter="url(#soft-shadow)">
    <text x="298" y="606" font-size="176" fill="url(#title-red)" textLength="249" lengthAdjust="spacingAndGlyphs">GIFT</text>
    <text x="592" y="606" font-size="176" fill="url(#title-blue)" textLength="309" lengthAdjust="spacingAndGlyphs">CARD</text>
  </g>
</svg>
</body>
</html>
```